International service dog training school needs web design

We need to upgrade our website. The website is https://brightmeadow.studio/
We help trainers and service dog programs learn how to train service dogs with the latest and most ethical training methods. We offer online and in-person coaching services. We would like to see designs that are engaging and communicate professionalism, expertise, and care for the dogs and people we work with. Please also keep the colors already in the logo in the design.

```html
<!DOCTYPE html>
<html lang="en">
<head>
<meta charset="utf-8">
<title>Bright Meadow Center for Medical Assistance Dogs</title>
<link href="https://fonts.googleapis.com/css2?family=Josefin+Sans:wght@600;700&family=Lato:wght@400;700&display=swap" rel="stylesheet">
<style>
:root{
  --teal:#1a9a8a;
  --teal-dark:#12806f;
  --blue:#1f5fb3;
  --blue-deep:#1b55a6;
  --mist:#e4f5f7;
  --ink:#1e1e1e;
  --grey:#8a8a8a;
  --white:#ffffff;
}
*{margin:0;padding:0;box-sizing:border-box}
html,body{width:1200px;height:4878px;overflow:hidden}
body{position:relative;background:var(--white);font-family:'Lato',sans-serif;color:var(--ink)}
.abs{position:absolute}
/* header */
.site-header{position:absolute;left:0;top:0;width:1200px;height:95px;background:var(--white);border-top:4px solid var(--blue);z-index:5}
.brand{position:absolute;left:144px;top:22px;display:flex;align-items:center;gap:12px}
.brand-dot{width:44px;height:44px;border-radius:50%;border:3px solid var(--teal)}
.brand-name{font-family:'Josefin Sans',sans-serif;font-weight:700;font-size:20px;color:var(--blue)}
.main-nav{position:absolute;left:450px;top:0;display:flex;height:95px}
.main-nav a{font-family:'Lato',sans-serif;font-weight:700;font-size:13px;color:var(--ink);text-decoration:none;text-transform:uppercase;padding:36px 16px 0;height:95px}
.main-nav a.active{background:var(--blue);color:var(--white);height:110px;border-radius:0 0 18px 18px;padding:36px 16px 0;width:105px;text-align:center}
/* hero */
.hero-photo{position:absolute;left:0;top:95px;width:1200px;height:740px;background:linear-gradient(180deg,#7a8a6e 0%,#5f8b3a 35%,#4f8a2a 70%,#6aa33a 100%)}
.hero-badge{position:absolute;left:142px;top:142px;width:462px;height:462px;border-radius:50%;background:var(--teal);text-align:center;color:var(--white)}
.hero-badge h1{font-family:'Josefin Sans',sans-serif;font-weight:700;font-size:46px;line-height:47px;text-transform:uppercase;margin-top:90px}
.btn{display:inline-block;width:174px;height:60px;line-height:56px;border:2px solid var(--teal);border-radius:30px;text-align:center;font-family:'Lato',sans-serif;font-weight:700;font-size:14px;color:var(--blue);text-transform:uppercase;text-decoration:none;background:transparent}
.btn.light{border-color:var(--white);color:var(--white)}
.hero-badge .btn{margin-top:36px}
.dots{position:absolute;left:1115px;top:340px}
.dots span{display:block;width:9px;height:9px;border-radius:50%;background:var(--white);margin-bottom:15px}
.dots span.on{background:var(--teal)}
/* intro */
.section-title{font-family:'Josefin Sans',sans-serif;font-weight:700;font-size:40px;line-height:48px;color:var(--ink)}
.intro{position:absolute;left:200px;top:800px;width:800px;text-align:center}
.intro p{font-size:13.5px;line-height:24px;color:#666;width:730px;margin:36px auto 50px}
/* feature rows */
.feature-text{position:absolute;width:480px}
.feature-text p{font-size:13.5px;line-height:24px;color:var(--grey);width:360px;margin:30px 0 34px}
.photo-circle{position:absolute;width:410px;height:410px}
/* book band */
.book{position:absolute;left:0;top:3960px;width:1200px;text-align:center;color:var(--white)}
.book h2{font-family:'Josefin Sans',sans-serif;font-weight:700;font-size:40px}
.book .subtitle{font-size:30px;line-height:45px;margin-top:36px}
.book .btn{margin-top:38px}
.book-cover{position:absolute;left:895px;top:4165px;width:160px;height:240px;background:linear-gradient(180deg,#f4f1ec 0%,#f4f1ec 45%,#c9a56a 75%,#b5202a 100%)}
/* closing */
.closing-photo{position:absolute;left:0;top:4440px;width:1200px;height:364px;background:linear-gradient(180deg,#e9eeee 0%,#f3f5f5 50%,#e2e6e4 100%)}
.closing{position:absolute;left:0;top:4515px;width:1200px;text-align:center}
.closing h2{font-family:'Josefin Sans',sans-serif;font-weight:700;font-size:40px;color:var(--ink);text-transform:uppercase}
.closing p{font-size:13.5px;color:#666;margin:22px 0 36px}
/* footer */
.site-footer{position:absolute;left:0;top:4804px;width:1200px;height:74px;background:var(--teal);color:var(--white);font-size:12.5px}
.site-footer .legal{position:absolute;left:144px;top:30px}
.site-footer .social{position:absolute;left:952px;top:28px;display:flex;gap:18px}
.site-footer .social span{width:20px;height:20px;border-radius:50%;background:var(--white)}
</style>
</head>
<body>

<header class="site-header">
  <div class="brand"><span class="brand-dot"></span><span class="brand-name">Helena Marsh Ph.D.</span></div>
  <nav class="main-nav">
    <a class="active" href="#">The Center</a>
    <a href="#">Helping Organizations</a>
    <a href="#">Teaching Trainers</a>
    <a href="#">Research Contact</a>
  </nav>
</header>

<div class="hero-photo" role="img" aria-label="Photo of a husky puppy sitting on a lead on green grass beside a training cone"></div>
<div class="hero-badge">
  <h1>The Bright<br>Meadow Center<br>for Medical<br>Assistance<br>Dogs</h1>
  <a class="btn light" href="#">Get Started</a>
</div>
<div class="dots"><span></span><span class="on"></span><span></span><span></span></div>

<svg class="abs" style="left:0;top:600px" width="1200" height="1320" viewBox="0 0 1200 1320" aria-hidden="true">
  <path d="M0 130 C250 150 420 20 720 30 C900 36 1060 60 1200 150 L1200 240 C1060 120 900 80 700 90 C420 100 250 180 0 160 Z" fill="var(--blue)"/>
  <path d="M0 140 C260 160 430 40 720 55 C920 65 1080 120 1200 230 L1200 320 C1060 160 900 105 700 110 C430 120 260 200 0 190 Z" fill="var(--teal)"/>
  <path d="M0 130 C280 205 440 80 720 88 C920 95 1080 170 1200 330 L1200 1320 L0 1320 Z" fill="var(--white)"/>
  <path d="M0 610 C300 690 700 560 1200 590 L1200 1290 C800 1180 400 1320 0 1250 Z" fill="var(--mist)"/>
</svg>

<section class="intro">
  <h2 class="section-title">The Bright Meadow Center For<br>Medical Assistance Dogs</h2>
  <p>The Bright Meadow Center for Medical Assistance Dogs was founded by Helena Marsh Ph.D. in response to demand for coaching from dog trainers, medical professionals, and service dog programs. Helena Marsh Ph.D. has helped hundreds of trainers and several programs both in the US and internationally, expand the type of dogs they could offer to include medical alert dogs. Specialized mostly in the training of diabetic alert dogs, seizure dogs, and psychiatric service dogs, Helena Marsh is also experienced in the training of mobility assistance dogs and autism dogs. The coaching is individually catered to meet the programs' needs.</p>
  <a class="btn" href="#">Read More</a>
</section>

<svg class="photo-circle" style="left:140px;top:1365px" viewBox="0 0 410 410" role="img" aria-label="Group photo of trainers in blue shirts with their dogs">
  <circle cx="213" cy="205" r="197" fill="var(--teal)"/><circle cx="197" cy="205" r="195" fill="#9aa3ab"/>
</svg>
<div class="feature-text" style="left:624px;top:1435px">
  <h3 class="section-title">Organization/Program<br>Consulting</h3>
  <p>Helping organizations get started, improve their training program, and add services</p>
  <a class="btn" href="#">Read More</a>
</div>

<div class="feature-text" style="left:144px;top:1992px">
  <h3 class="section-title">Professional coaching/<br>teaching for dog<br>trainers</h3>
  <p>Helping dog trainers improve their skills and learn about service dog training and medical alert dog training.</p>
  <a class="btn" href="#">Read More</a>
</div>
<svg class="photo-circle" style="left:650px;top:1945px" viewBox="0 0 410 410" role="img" aria-label="Photo of a trainer working with a black dog on a lead indoors">
  <circle cx="213" cy="205" r="197" fill="var(--teal)"/><circle cx="197" cy="205" r="195" fill="#8c8378"/>
</svg>

<svg class="photo-circle" style="left:140px;top:2405px" viewBox="0 0 410 410" role="img" aria-label="Photo of a detection dog in a vest sniffing metal cans on a tiled floor">
  <circle cx="213" cy="205" r="197" fill="var(--teal)"/><circle cx="197" cy="205" r="195" fill="#c9bfb3"/>
</svg>
<div class="feature-text" style="left:624px;top:2472px">
  <h3 class="section-title">Collaborating in<br>Research Projects</h3>
  <p>Collaborating in research studies in the field of Medical Detection Dogs.</p>
  <a class="btn" href="#">Read More</a>
</div>

<div class="feature-text" style="left:144px;top:2934px">
  <h3 class="section-title">Presentations and<br>Seminars</h3>
  <p>Sharing knowledge about service dogs and medical detection.</p>
  <a class="btn" href="#">Read More</a>
</div>
<svg class="photo-circle" style="left:650px;top:2865px" viewBox="0 0 410 410" role="img" aria-label="Photo of an audience seated in a seminar hall facing a projection screen">
  <circle cx="213" cy="205" r="197" fill="var(--teal)"/><circle cx="197" cy="205" r="195" fill="#5f5a58"/>
</svg>

<svg class="photo-circle" style="left:140px;top:3327px" viewBox="0 0 410 410" role="img" aria-label="Photo of a service dog in a red vest looking out an airport window">
  <circle cx="213" cy="205" r="197" fill="var(--teal)"/><circle cx="197" cy="205" r="195" fill="#a9a49a"/>
</svg>
<div class="feature-text" style="left:624px;top:3392px">
  <h3 class="section-title">International<br>services</h3>
  <p>Fluent in both English and French, in-person and online coaching around the world.</p>
  <a class="btn" href="#">Read More</a>
</div>

<svg class="abs" style="left:0;top:3760px" width="1200" height="730" viewBox="0 0 1200 730" aria-hidden="true">
  <path d="M0 20 C300 80 800 60 1200 0 L1200 640 C900 520 400 660 0 720 Z" fill="var(--blue-deep)"/>
</svg>
<section class="book">
  <h2>New book from Helena Marsh Ph.D.!</h2>
  <p class="subtitle">Choosing And Raising Your Service Dog:<br>How to Thrive in Public Access Work</p>
  <a class="btn light" href="#">Click Here</a>
</section>
<div class="book-cover" role="img" aria-label="Book cover showing a yellow service dog in a vest"></div>

<div class="closing-photo" role="img" aria-label="Faded photo of a service dog resting beside its handler"></div>
<svg class="abs" style="left:0;top:4380px" width="1200" height="140" viewBox="0 0 1200 140" aria-hidden="true">
  <path d="M0 100 C400 40 800 130 1200 88 L1200 0 L0 0 Z" fill="var(--blue-deep)"/>
</svg>
<section class="closing">
  <h2>Staying Ahead</h2>
  <p>Science-based and ethical training methods for the modern service dog trainer.</p>
  <a class="btn" href="#">Get Started</a>
</section>

<footer class="site-footer">
  <div class="legal">© 2021 Company Name. All rights reserved &nbsp;|&nbsp; Privacy &nbsp;|&nbsp; Terms of Use</div>
  <div class="social"><span></span><span></span><span></span></div>
</footer>

</body>
</html>
```